Ledgerwise Forge - WordPress Theme & Logo

Design a logo and Wordpress website design for Ledgerwise Forge. Ledgerwise Forge provides cryptocurrency development services to clients who need a team to create & continue developing a new cryptocurrency or who want to replace their current cryptocurrency development team. more details in the attached document.
Updates

Target Market(s)

Entrepreneurs who are building a business / platform that makes use of an underlying cryptocurrency.

Logo Text

LF or Ledgerwise Forge

Coding

Coded - Design and coding required

Font styles to use
Sans Serif

Requirements
Must have
• Professional logo, complete coded Wordpress theme for all pages, containing all specified links and buttons
Nice to have
• It would be nice if the buttons that are meant to integrate with Dealtrail contain the necessary code for that. I can provide any necessary Dealtrail details from my account.
Should not have
• Slow loading time

```html
<!DOCTYPE html>
<html lang="en">
<head>
<meta charset="utf-8">
<title>Ledgerwise Forge</title>
<link href="https://fonts.googleapis.com/css2?family=Montserrat:wght@400;700;800&family=Roboto:wght@400;500;700&display=swap" rel="stylesheet">
<style>
:root{
  --blue:#0a57a8;
  --blue-dark:#084a90;
  --ink:#111111;
  --text:#555555;
  --muted:#6b6b6b;
  --soft:#f5f5f5;
  --white:#ffffff;
  --star:#f5c518;
}
*{box-sizing:border-box;margin:0;padding:0}
html,body{width:1200px;height:3588px;overflow:hidden}
body{position:relative;font-family:'Roboto',sans-serif;color:var(--text);background:var(--white)}
.abs{position:absolute}
.heading{font-family:'Montserrat',sans-serif;color:var(--ink);font-weight:400;text-align:center}
.heading b{font-weight:800}
.btn{position:absolute;display:flex;align-items:center;justify-content:center;gap:8px;background:var(--blue);color:var(--white);border-radius:22px;font-family:'Roboto',sans-serif;font-weight:500;font-size:15px}
.btn .arrow{width:14px;height:14px;border-radius:50%;background:var(--white);position:relative}
.btn .arrow::after{content:"";position:absolute;left:4px;top:4px;width:4px;height:4px;border-top:2px solid var(--blue);border-right:2px solid var(--blue);transform:rotate(45deg)}

/* header */
.site-header{position:absolute;left:0;top:0;width:1200px;height:100px;z-index:3}
.brand{position:absolute;left:68px;top:22px;display:flex;align-items:center;gap:14px}
.brand-mark{width:52px;height:52px;border-radius:50%;border:9px solid var(--blue)}
.brand-name{font-family:'Montserrat',sans-serif;font-weight:700;font-size:19px;color:var(--ink);line-height:1.15}
.brand-name small{display:block;font-family:'Roboto',sans-serif;font-weight:500;font-size:13px;color:#333}
.main-nav{position:absolute;left:344px;top:38px;display:flex;gap:23px;font-size:15px;color:#222}
.main-nav .active{color:var(--blue)}
.header-btn{left:891px;top:29px;width:240px;height:39px;font-size:15px}

/* hero */
.hero-photo{position:absolute;left:0;top:0;width:1200px;height:816px;background:linear-gradient(180deg,#f3f4f8 0%,#eceef3 32%,#c9c3bd 55%,#8a7e74 78%,#4e4a4a 100%)}
.hero-title{position:absolute;left:0;top:154px;width:1200px;font-size:39px;line-height:47px}
.hero-text{position:absolute;left:205px;top:270px;width:790px;text-align:center;font-size:15px;line-height:27.5px;color:#222}
.hero-btn{left:471px;top:375px;width:257px;height:40px}

/* why */
.why-title{position:absolute;left:0;top:895px;width:1200px;font-size:37px}
.hex-card{position:absolute;top:995px;width:260px;height:290px}
.hex-card h3{position:absolute;left:0;top:122px;width:260px;text-align:center;font-size:20px;font-weight:500;color:var(--ink)}
.hex-card p{position:absolute;left:20px;top:160px;width:220px;text-align:center;font-size:14px;line-height:23.5px;color:var(--muted)}

/* who */
.who-panel{position:absolute;left:589px;top:1374px;width:611px;height:392px;background:var(--soft)}
.who-photo{position:absolute;left:0;top:1374px;width:589px;height:392px;background:linear-gradient(160deg,#b9bdc4 0%,#6d7078 45%,#3d3f47 100%)}
.who-title{position:absolute;left:643px;top:1428px;font-size:40px;text-align:left}
.who-text{position:absolute;left:643px;top:1497px;width:455px;font-size:14px;line-height:26.7px;color:var(--muted)}
.who-btn{left:643px;top:1658px;width:166px;height:44px}

/* testimonials */
.say-title{position:absolute;left:0;top:1860px;width:1200px;font-size:40px}
.quote{position:absolute;top:1988px;width:309px;height:190px;background:var(--white);border-top:3px solid var(--blue);border-radius:10px;box-shadow:0 4px 16px rgba(0,0,0,.10)}
.quote p{position:absolute;left:22px;top:66px;width:265px;text-align:center;font-size:14.5px;line-height:25.6px;color:#444}
.avatar{position:absolute;top:1945px;width:90px;height:90px;border-radius:50%;background:linear-gradient(180deg,#d9d9d9,#8c8c8c);border:3px solid var(--white);box-shadow:0 2px 6px rgba(0,0,0,.15)}
.person{position:absolute;top:2202px;width:309px;text-align:center;font-size:15px;font-weight:500;color:var(--ink)}
.person small{font-size:10px;font-weight:400;color:#333}
.stars{position:absolute;top:2225px;width:309px;text-align:center;color:var(--star);font-size:13px;letter-spacing:1px}

/* services */
.services{position:absolute;left:0;top:2352px;width:1200px;height:856px;background:var(--soft)}
.services-title{position:absolute;left:0;top:2405px;width:1200px;font-size:40px}
.services-intro{position:absolute;left:120px;top:2464px;width:960px;text-align:center;font-size:14px;line-height:24.5px;color:var(--muted)}
.services-intro p+p{margin-top:12px}
.service-feature{position:absolute;left:433px;top:2633px;width:335px;height:370px;background:var(--white);border-radius:22px;border-bottom:4px solid var(--blue);box-shadow:0 4px 20px rgba(0,0,0,.08)}
.service{position:absolute;top:2655px;width:300px;text-align:center}
.service .icon{width:116px;height:116px;border-radius:50%;background:var(--blue);margin:0 auto;display:flex;align-items:center;justify-content:center}
.service h3{margin-top:26px;font-size:19px;font-weight:500;color:var(--ink)}
.service p{margin-top:12px;font-size:14px;line-height:24.7px;color:var(--muted)}
.service .more{position:absolute;left:0;top:302px;width:300px;display:flex;justify-content:center;align-items:center;gap:7px;color:var(--blue);font-weight:700;font-size:14px}
.more .dot{width:14px;height:14px;border-radius:50%;background:var(--blue);position:relative}
.more .dot::after{content:"";position:absolute;left:3px;top:4px;width:4px;height:4px;border-top:2px solid #fff;border-right:2px solid #fff;transform:rotate(45deg)}
.chev{position:absolute;top:2815px;width:22px;height:22px;border-top:4px solid #9a9a9a;border-right:4px solid #9a9a9a}
.services-btn{left:471px;top:3074px;width:257px;height:40px}

/* footer */
.site-footer{position:absolute;left:0;top:3208px;width:1200px;height:380px;background:var(--blue);color:var(--white)}
.site-footer h4{position:absolute;top:90px;font-size:18px;font-weight:700}
.contact-list{position:absolute;left:110px;top:130px;width:240px;font-size:14px;line-height:21px}
.contact-list li{list-style:none;display:flex;gap:12px;margin-bottom:13px}
.contact-list svg{flex:0 0 14px;margin-top:3px}
.link-col{position:absolute;top:128px;list-style:none;font-size:14px;line-height:26.5px}
.subscribe-field{position:absolute;left:714px;top:3338px;width:238px;height:43px;border-radius:22px;background:var(--white);color:#888;font-size:11px;padding:15px 22px}
.subscribe-btn{position:absolute;left:965px;top:3338px;width:122px;height:43px;border-radius:22px;background:#1b1b1b;color:#fff;font-weight:700;font-size:16px;display:flex;align-items:center;justify-content:center}
.consent{position:absolute;left:711px;top:3408px;font-size:13px;font-weight:500;display:flex;gap:9px;align-items:center}
.social{position:absolute;top:3448px;width:32px;height:32px;border-radius:50%;border:1.5px solid var(--white)}
.social span{position:absolute;left:11px;top:11px;width:8px;height:8px;border-radius:50%;background:var(--white)}
.footer-rule{position:absolute;left:110px;top:3515px;width:980px;height:1px;background:rgba(255,255,255,.25)}
.copyright{position:absolute;left:0;top:3538px;width:1200px;text-align:center;font-size:13px}
</style>
</head>
<body>

<div class="hero-photo" role="img" aria-label="Photo of a team of four colleagues smiling around a meeting table"></div>

<header class="site-header">
  <div class="brand"><span class="brand-mark"></span><div class="brand-name">Ledgerwise Forge<small>Crypto Development</small></div></div>
  <nav class="main-nav"><span class="active">Home</span><span>About Us</span><span>Our Services</span><span>Service Tiers</span><span>Testimonials</span><span>Blog</span></nav>
  <div class="btn header-btn">Schedule a Free Consultation</div>
</header>

<h1 class="heading hero-title"><b>Your own cryptocurrency. Secure,</b> easy to<br>use, &amp; built by an expert team.</h1>
<p class="hero-text">Ledgerwise Forge adds professionalism to cryptocurrency development. Our done-for-you service covers everything from development and IT operations to ongoing support. You have access to a full team, for less than the typical cost of a single developer.</p>
<div class="btn hero-btn">Schedule a Free Consultation <span class="arrow"></span></div>

<h2 class="heading why-title"><b>Why choose</b> Ledgerwise Forge</h2>

<div class="hex-card" style="left:171px">
  <svg width="260" height="290" viewBox="0 0 260 290"><defs><filter id="sh" x="-20%" y="-20%" width="140%" height="140%"><feDropShadow dx="0" dy="4" stdDeviation="7" flood-opacity=".12"/></filter></defs>
    <polygon points="130,10 252,75 252,220 130,285 8,220 8,75" fill="#fff" filter="url(#sh)"/>
    <polygon points="130,0 211,47 130,94 49,47" fill="#0a57a8"/>
    <g fill="none" stroke="#fff" stroke-width="2"><polygon points="115,38 145,38 155,50 130,75 105,50"/><line x1="105" y1="50" x2="155" y2="50"/><polyline points="120,38 130,50 140,38"/><line x1="130" y1="50" x2="130" y2="75"/></g>
  </svg>
  <h3>Value</h3><p>A team of experts, regular updates, and fixed costs</p>
</div>
<div class="hex-card" style="left:470px">
  <svg width="260" height="290" viewBox="0 0 260 290"><polygon points="130,10 252,75 252,220 130,285 8,220 8,75" fill="#fff" filter="url(#sh)"/>
    <polygon points="130,0 211,47 130,94 49,47" fill="#0a57a8"/>
    <g fill="none" stroke="#fff" stroke-width="2"><circle cx="130" cy="38" r="11"/><circle cx="130" cy="38" r="4"/><path d="M108 64 q10 -8 20 0 h16 l10 -8"/><path d="M108 70 h30 l18 -12"/></g>
  </svg>
  <h3>Support</h3><p>Receive advice and other services, beyond development.</p>
</div>
<div class="hex-card" style="left:769px">
  <svg width="260" height="290" viewBox="0 0 260 290"><polygon points="130,10 252,75 252,220 130,285 8,220 8,75" fill="#fff" filter="url(#sh)"/>
    <polygon points="130,0 211,47 130,94 49,47" fill="#0a57a8"/>
    <g fill="none" stroke="#fff" stroke-width="2"><rect x="112" y="24" width="26" height="36"/><line x1="117" y1="32" x2="133" y2="32"/><line x1="117" y1="39" x2="133" y2="39"/><line x1="117" y1="46" x2="128" y2="46"/><line x1="148" y1="30" x2="134" y2="60"/><line x1="110" y1="66" x2="152" y2="66"/></g>
  </svg>
  <h3>Commitment</h3><p>Enjoy regular updates and new features.</p>
</div>

<div class="who-photo" role="img" aria-label="Photo of three colleagues working together at a laptop"></div>
<div class="who-panel"></div>
<h2 class="heading who-title"><b>Who</b> We Are</h2>
<p class="who-text">In addition to creating and enhancing cryptocurrencies for clients, the Ledgerwise Forge team has been running the Quillon cryptocurrency since 2017. We prefer long-term relationships, enabling us to deliver the very highest quality and giving you peace of mind that you've got aprofessional and trustworthy team at your side.</p>
<div class="btn who-btn">READ MORE <span class="arrow"></span></div>

<h2 class="heading say-title"><b>What Our</b> Clients Say</h2>
<div class="quote" style="left:111px"><p>Sed ut perspiciatis unde omnis iste natus error sit voluptatem accusantium doloremque laudantium, totam rem aperiam, eaque ipsa</p></div>
<div class="quote" style="left:445px"><p>Sed ut perspiciatis unde omnis iste natus error sit voluptatem accusantium doloremque laudantium, totam rem aperiam, eaque ipsa</p></div>
<div class="quote" style="left:779px"><p>Sed ut perspiciatis unde omnis iste natus error sit voluptatem accusantium doloremque laudantium, totam rem aperiam, eaque ipsa</p></div>
<div class="avatar" style="left:220px" role="img" aria-label="Portrait of Dana Whitlow"></div>
<div class="avatar" style="left:554px" role="img" aria-label="Portrait of Lena Orsik"></div>
<div class="avatar" style="left:888px" role="img" aria-label="Portrait of Marco Pell"></div>
<div class="person" style="left:111px">Dana Whitlow, <small>Chairman NCV</small></div>
<div class="person" style="left:445px">Lena Orsik, <small>Project Manager</small></div>
<div class="person" style="left:779px">Marco Pell, <small>Chairman NCV</small></div>
<div class="stars" style="left:111px">★★★★★</div>
<div class="stars" style="left:445px">★★★★★</div>
<div class="stars" style="left:779px">★★★★★</div>

<section class="services"></section>
<h2 class="heading services-title"><b>Our</b> Services</h2>
<div class="services-intro">
  <p>Ledgerwise Forge provides a complete service that handles the development, IT operations and support for your cryptocurrency. Cryptocurrency development can be difficult and complex, and a quality development team is hard to find and expensive. expensive.</p>
  <p>Ledgerwise Forge has an experienced team that has helped several clients launch and enhance their cryptocurrencies, including successfully running the Quillon cryptocurrency since 2017, and writing a next-generation cryptocurrency from scratch.</p>
</div>
<div class="service-feature"></div>
<span class="chev" style="left:40px;transform:rotate(-135deg)"></span>
<span class="chev" style="left:1132px;transform:rotate(45deg)"></span>

<div class="service" style="left:102px">
  <div class="icon"><svg width="60" height="60" viewBox="0 0 60 60" fill="none" stroke="#fff" stroke-width="2"><rect x="18" y="6" width="24" height="40" rx="3"/><circle cx="30" cy="24" r="7"/><path d="M14 56 v-12 q0 -6 6 -4 l4 4"/><line x1="8" y1="14" x2="8" y2="30"/><line x1="52" y1="14" x2="52" y2="30"/></svg></div>
  <h3>Blockchain Creation &amp; Launch</h3>
  <p>Base fixed price for cryptocurrency development &amp; launch–would be customizable based on client requirements</p>
  <div class="more">READ MORE <span class="dot"></span></div>
</div>
<div class="service" style="left:450px">
  <div class="icon"><svg width="60" height="60" viewBox="0 0 60 60" fill="none" stroke="#fff" stroke-width="2"><rect x="10" y="22" width="34" height="24" rx="2"/><line x1="6" y1="50" x2="48" y2="50"/><circle cx="38" cy="18" r="10"/><circle cx="38" cy="18" r="4"/></svg></div>
  <h3>Basic offering</h3>
  <p>Lower cost per month<br>Slower release schedule<br>Client assists with testing new releases<br>Less input into future roadmap/features</p>
  <div class="more">READ MORE <span class="dot"></span></div>
</div>
<div class="service" style="left:796px">
  <div class="icon"><svg width="60" height="60" viewBox="0 0 60 60" fill="none" stroke="#fff" stroke-width="2"><polygon points="30,6 50,14 30,22 10,14"/><path d="M18 18 v6 q12 6 24 0 v-6"/><rect x="8" y="30" width="32" height="18" rx="2"/><circle cx="24" cy="39" r="4"/><circle cx="44" cy="44" r="9"/></svg></div>
  <h3>Full service offering</h3>
  <p>Mid-range cost per month<br>Releases every 1.5 - 2 months<br>Client can help request/prioritize new<br>Full testing by my team prior to release</p>
  <div class="more">READ MORE <span class="dot"></span></div>
</div>
<div class="btn services-btn">Schedule a Free Consultation <span class="arrow"></span></div>

<footer class="site-footer">
  <h4 style="left:110px">Contact Us</h4>
  <h4 style="left:395px">Links</h4>
  <h4 style="left:710px">Subscribe for Updates</h4>
  <ul class="contact-list">
    <li><svg width="14" height="16" viewBox="0 0 14 16"><path d="M7 0 a6 6 0 0 1 6 6 c0 4 -6 10 -6 10 s-6 -6 -6 -10 a6 6 0 0 1 6 -6z" fill="#fff"/><circle cx="7" cy="6" r="2.2" fill="#0a57a8"/></svg><span>3501 Lorem ipsum dolor sit amet, consectetur</span></li>
    <li><svg width="14" height="12" viewBox="0 0 14 12"><rect width="14" height="11" rx="1" fill="#fff"/><path d="M1 1 l6 5 l6 -5" stroke="#0a57a8" fill="none" stroke-width="1.4"/></svg><span>info@ledgerwiseforge.example</span></li>
    <li><svg width="14" height="14" viewBox="0 0 14 14"><path d="M3 0 l3 3 -2 2 q2 4 5 5 l2 -2 3 3 -2 3 q-8 -1 -12 -12z" fill="#fff"/></svg><span>555.014.2290</span></li>
    <li><svg width="14" height="14" viewBox="0 0 14 14"><rect x="0" y="4" width="14" height="10" rx="1" fill="#fff"/><rect x="3" y="0" width="8" height="5" fill="#fff"/><rect x="3" y="7" width="8" height="2" fill="#0a57a8"/></svg><span>(555)&nbsp; 010 - 7788</span></li>
  </ul>
  <ul class="link-col" style="left:395px"><li>Home</li><li>About Us</li><li>Our Services</li><li>Service Tiers</li><li>Testimonials</li></ul>
  <ul class="link-col" style="left:521px"><li>Terms &amp; Condition</li><li>Privacy Policy</li><li>Updates</li><li>Support</li><li>Contact</li></ul>
  <div class="footer-rule"></div>
  <div class="copyright">© 2021&nbsp; Ledgerwise Forge&nbsp; |&nbsp; All Rights Reserved</div>
</footer>
<div class="subscribe-field">Emaill Address</div>
<div class="subscribe-btn">SUBMIT</div>
<div class="consent"><svg width="13" height="13" viewBox="0 0 13 13"><rect x=".7" y=".7" width="11.6" height="11.6" rx="2" fill="none" stroke="#fff" stroke-width="1.3"/><path d="M3 6.5 l2.5 2.5 l5 -6" stroke="#fff" stroke-width="1.6" fill="none"/></svg>Yes, Please Contact me.</div>
<div class="social" style="left:711px" aria-label="Social profile"><span></span></div>
<div class="social" style="left:753px" aria-label="Social profile"><span></span></div>
<div class="social" style="left:795px" aria-label="Social profile"><span></span></div>

</body>
</html>
```